Wordpress Theme for Medical Clinics

** Please view updated Sitemap2.pdf doc to clarify some confusion ***

This is a multiuser WordPress subscription site for medical clinics. Please see attachment for sitemap. Please do not include extra content like social media icons, search bars, or images. If you have questions, please ask for clarification.
The site contains the following pages and sub-pages:

1. Home
2. Our Clinic
2a. Our Clinic > Mission
2b. Our Clinic > Services
2c. Our Clinic > Clinic Policies
2d. Our Clinic > Schedules
3. Our Staff
3a. Our Staff > [Staff member page]
4. Resources
4a. Resources > Patient Health (index)
4b. Resources > Patient Health (index) > [post]
4c. Resources > Links
4d. Resources > Forms
5. Alerts
5a. Alerts > [Alert Page]
6. Contact Us

Includes the Following Pages, Subpages, and Content
1. Home
a. About Us
b. Our Staff
c. Bulletins
d. Accepting New Patients (shown as an alert widget)
e. Links
i. Physician Toolbox
ii. Book an Appointment
f. Clinic Policies
i. Show first 3 policies (e.g. Late Arrivals, Missed Appointments, Fees)
ii. Link to Clinic Policies page
g. Primary widget (displayed on all pages)
i. Hours of operation
ii. Contact Info
1. Tel
2. Fax
3. Email
4. Address
5. Get directions (link to Map Directions)
2. Our Clinic
a. Main Page
i. Clinic Name
ii. Overview
iii. Languages Spoken
iv. Secondary Navigation
1. Mission
2. Services
3. Clinic Policies
4. Schedules (see attachment)
b. Our Clinic > Mission
c. Our Clinic > Services
i. For each service include service TITLE and DESCRIPTION
d. Our Clinic > Clinic Policies
i. For each policy include policy TITLE and DESCRIPTION
ii. Include the following policies in mockup
1. Late arrivals
2. Missed appointments
3. Fees for missed appointments
4. Referrals and follow-ups
5. Services not covered by RDA
6. Information for LTF patients
7. Medical Legal Reports
e. Our Clinic > Schedules
3. Our Staff
a. Main Page
i. Display a list of staff members. Include NAME and DESIGNATION
b. Our Staff > [Staff Name]
i. Include NAME, PICTURE, DESIGNATION, and BIO
4. Resources
a. Resources > Patient Health
i. Main Page
1. Posts (ordered by date)
a. Title
b. Summary
2. Side Navigation
a. Post Categories
ii. Patient Health > [post title]
1. Title
2. Post Category
3. Date
4. Author
5. Summary
6. Body
b. Resources > Links
1. Secondary Navigation - Categories
a. Sample Categories:
i. Local Services
ii. RDA and Drug Coverage
iii. Mental Health Resources
2. Category page
a. Include the following links in the 'Local Services' category
i. Hypertension clinics
ii. Home Care services
iii. Vaccine Clinics
c. Resources > Forms
i. Display a table with form TITLE and CATEGORY
ii. Side Navigation
1. Form Categories
a. Use the following sample Categories
i. Referrals
ii. Insurance
iii. Intake
iv. Discharge
v. Waivers
5. Alerts
a. Main page
i. List of all Alert posts
1. Include post TITLE as a link to the post
ii. Side Navigation
1. Alerts Archive
a. shown as Month + Number of posts
iii. Alerts > [Alert page]
1. Include TITLE, DATE, AUTHOR, BODY
6. Contact Us
a. Map
b. Hours of operation
c. Address
d. Phone number
e. Fax number
e. Fax number
f. Map
g. Email

Design notes:
- fixed width
- responsive (need designs for mobile, tablet, and desktop)
- simple, dark font, white background
- use Font Awesome icons where needed
- user adds own logo

Target Market(s)

Medical Clinics

Industry/Entity Type

Medical

Number of Pages Required

5+ page

Font styles to use
Serif
Sans Serif

Requirements
Must have
• Please keep designs very simple.
• Examples:
• https://www.quolbin.com/install
• http://www.ventrohax.com/company/about-us
• http://brindlequota.org/
• http://www.trosk.com/
Should not have
• Minimal or no use of shadows and gradients

```html
<!DOCTYPE html>
<html lang="en">
<head>
<meta charset="utf-8">
<title>Clinic Name – Home</title>
<link href="https://fonts.googleapis.com/css2?family=Open+Sans:wght@400;600;700&display=swap" rel="stylesheet">
<style>
:root{
  --blue:#5fc3ec;
  --blue-dark:#3fa9dc;
  --yellow:#fcd96a;
  --ink:#222831;
  --text:#555c66;
  --muted:#8a929c;
  --line:#e3e8ee;
  --pale:#eef6fc;
  --white:#ffffff;
}
*{box-sizing:border-box;margin:0;padding:0}
html,body{width:1200px;height:3193px;overflow:hidden;background:var(--white)}
body{font-family:"Open Sans",Arial,sans-serif;color:var(--text);font-size:13px;position:relative}
a{color:inherit;text-decoration:none}
.abs{position:absolute}

/* top bar + header */
.topbar{top:0;left:0;width:1200px;height:36px;font-size:12px;color:var(--blue)}
.topbar span{position:absolute;top:11px}
.header{top:36px;left:0;width:1200px;height:118px}
.brand{position:absolute;left:72px;top:44px;display:flex;align-items:center;gap:12px;font-size:22px;font-weight:600;color:var(--blue-dark);letter-spacing:.5px}
.brand i{width:30px;height:30px;background:var(--blue);display:block;border-radius:4px}
.nav{position:absolute;top:52px;left:480px;display:flex;gap:0;font-size:12px;font-weight:600;color:#6b737c;letter-spacing:.5px}
.nav a{width:auto;margin-right:52px}
.nav a.active{color:var(--blue)}

/* hero */
.hero{top:154px;left:0;width:1200px;height:583px;background:linear-gradient(90deg,#e6ecf1 0%,#dde6ed 45%,#cfdbe4 100%)}
.hero-figure{position:absolute;left:560px;top:0;width:560px;height:583px;background:radial-gradient(ellipse at 50% 55%,#f3f4f6 0%,#dfe6ec 70%,rgba(221,230,236,0) 100%)}
.hero-copy{position:absolute;left:72px;top:130px;width:440px}
.hero h1{font-size:27px;line-height:34px;font-weight:700;color:var(--ink)}
.hero h1 span{font-weight:400;display:block}
.hero p{margin-top:14px;font-size:13px;line-height:21px;color:#4a525c}
.btn-outline{display:inline-block;margin-top:28px;border:2px solid var(--ink);color:var(--ink);font-size:12px;font-weight:700;padding:10px 16px}
.arrow{position:absolute;top:273px;width:30px;height:34px;background:#333a42;display:flex;align-items:center;justify-content:center}

/* info band */
.info{top:737px;height:381px;color:var(--white)}
.info .badge{position:absolute;top:-40px;width:76px;height:76px;border-radius:50%;display:flex;align-items:center;justify-content:center}
.info h3{position:absolute;top:48px;font-size:15px;font-weight:700;letter-spacing:.3px}
.patients{left:0;width:434px;background:var(--blue)}
.hours{left:434px;width:332px;background:var(--yellow);color:var(--ink)}
.contact{left:766px;width:434px;background:var(--blue)}
.patients p{position:absolute;left:90px;top:84px;font-size:12px}
.btn-light{position:absolute;left:90px;top:136px;border:2px solid var(--white);font-size:12px;font-weight:700;padding:10px 14px;color:var(--white)}
.rows{position:absolute;list-style:none;font-size:11.5px}
.rows li{display:flex;height:41px;align-items:center;border-top:1px solid rgba(0,0,0,.08)}
.hours .rows{left:18px;top:68px;width:300px}
.hours .rows li{justify-content:space-between;padding:0 0 0 0}
.hours .rows b{font-weight:700}
.contact .rows{left:46px;top:68px;width:360px}
.contact .rows li{border-color:rgba(255,255,255,.25);align-items:flex-start;padding-top:13px}
.contact .rows b{width:194px;font-weight:700;font-size:11px}
.contact .rows li.tall{height:80px}

/* section titles */
.sec-title{text-align:center;left:0;width:1200px}
.sec-title small{display:block;font-size:14px;color:var(--ink);letter-spacing:1px}
.sec-title h2{font-size:36px;font-weight:700;color:var(--ink);letter-spacing:1px;line-height:42px}
.sec-title i{display:block;width:40px;height:3px;background:var(--yellow);margin:6px auto 0}

/* about */
.about{top:1118px;left:0;width:1200px;height:417px;background:linear-gradient(180deg,#ffffff,#f7f9fb)}
.about-text{position:absolute;left:165px;top:186px;width:870px;text-align:center;font-size:13px;line-height:26px;color:#3e454e}
.about-text p+p{margin-top:14px}

/* alerts + staff */
.team{top:1535px;left:0;width:1200px;height:509px;background:var(--pale)}
.col-head{position:absolute;top:50px;font-size:17px;font-weight:700;color:var(--ink);display:flex;align-items:center;gap:10px;letter-spacing:.5px}
.pager{position:absolute;top:54px;font-size:16px;color:#6b737c;letter-spacing:3px}
.alert{position:absolute;left:72px;width:336px;height:100px}
.alert .date{position:absolute;left:0;top:0;width:70px;height:76px;border:2px solid var(--ink);text-align:center;color:var(--ink)}
.alert .date b{display:block;font-size:26px;line-height:32px;margin-top:6px}
.alert .date span{font-size:11px;font-weight:600}
.alert h4{position:absolute;left:104px;top:0;font-size:11px;font-weight:700;color:var(--ink);line-height:16px}
.alert p{position:absolute;left:104px;top:40px;font-size:11.5px;line-height:18px;color:var(--muted)}
.staff{position:absolute;width:330px;height:144px;background:var(--white)}
.staff .photo{position:absolute;left:0;top:0;width:140px;height:144px;background:linear-gradient(180deg,#b9c6cf,#6fa8c9)}
.staff h4{position:absolute;left:168px;top:42px;font-size:11px;font-weight:700;color:var(--ink)}
.staff span{position:absolute;left:168px;top:60px;font-size:11px;color:var(--muted)}
.staff a{position:absolute;right:12px;bottom:10px;font-size:10.5px;color:var(--ink);border-top:1px solid var(--line);width:150px;text-align:right;padding-top:6px}

/* policies */
.policies{top:2044px;left:0;width:1200px;height:537px}
.policy{position:absolute;top:159px;width:333px;height:240px;border:2px solid #d8eefa;padding:0 32px}
.policy svg{position:absolute;left:32px;top:36px}
.policy h4{position:absolute;left:32px;top:94px;font-size:12px;font-weight:700;color:var(--ink)}
.policy p{position:absolute;left:32px;top:126px;width:260px;font-size:12px;line-height:19px;color:var(--text)}
.policy a{position:absolute;left:32px;top:200px;font-size:11px;color:var(--ink)}
.btn-blue{position:absolute;left:490px;top:441px;width:223px;height:43px;border:2px solid var(--blue);color:var(--blue-dark);font-size:12px;font-weight:700;display:flex;align-items:center;justify-content:center;letter-spacing:.3px}

/* location */
.location{top:2581px;left:0;width:1200px;height:128px;background:var(--pale)}
.map{top:2709px;left:0;width:1200px;height:431px;background:linear-gradient(135deg,#e9e6df 0%,#e2e4de 50%,#dfe3e4 100%)}
.map-card{position:absolute;left:580px;top:173px;width:192px;height:98px;background:var(--blue);color:var(--white);padding:14px 16px;font-size:11px;line-height:15px}
.map-card b{display:block;font-size:12px;margin-bottom:6px}
.map-card i{position:absolute;left:18px;bottom:-12px;border-left:10px solid transparent;border-right:10px solid transparent;border-top:12px solid var(--blue)}

/* footer */
.footer{top:3140px;left:0;width:1200px;height:53px;font-size:11px;color:#3e454e}
.footer span{position:absolute;top:19px}
</style>
</head>
<body>

<div class="abs topbar">
  <span style="left:802px">Call : 555 010 0199</span>
  <span style="left:972px">Email : hello@mendwell.co</span>
</div>

<header class="abs header">
  <div class="brand"><i></i>CLINIC NAME</div>
  <nav class="nav">
    <a class="active" href="#">HOME</a>
    <a href="#">OUR CLINIC</a>
    <a href="#">OUR STAFF</a>
    <a href="#">RESOURCES</a>
    <a href="#">ALERTS</a>
    <a href="#">CONTACT US</a>
  </nav>
</header>

<section class="abs hero">
  <div class="hero-figure" role="img" aria-label="Smiling physician in a white coat with a stethoscope"></div>
  <div class="hero-copy">
    <h1>FREE ONLINE LOREM IPSUM<span>GENERATOR WITH FEATURES</span></h1>
    <p>Lorem Ipsum is simply dummy text of the printing and typesetting industry. Lorem Ipsum has been the industry's standard dummy text ever since the 1500s.</p>
    <a class="btn-outline" href="#">CONTACT US</a>
  </div>
  <div class="arrow" style="left:0"><svg width="10" height="14" viewBox="0 0 10 14"><path d="M8 1 2 7l6 6" fill="none" stroke="#fff" stroke-width="2"/></svg></div>
  <div class="arrow" style="right:0"><svg width="10" height="14" viewBox="0 0 10 14"><path d="M2 1l6 6-6 6" fill="none" stroke="#fff" stroke-width="2"/></svg></div>
</section>

<section class="abs info patients">
  <div class="badge" style="left:92px;background:var(--blue)"><svg width="26" height="28" viewBox="0 0 26 28"><circle cx="13" cy="8" r="7" fill="#fff"/><path d="M0 28c0-8 6-12 13-12s13 4 13 12z" fill="#fff"/></svg></div>
  <h3 style="left:90px">NEW PATIENTS</h3>
  <p>Accepting new patients</p>
  <a class="btn-light" href="#">CONTACT US</a>
</section>

<section class="abs info hours">
  <div class="badge" style="left:20px;background:var(--yellow)"><svg width="28" height="28" viewBox="0 0 28 28"><circle cx="14" cy="14" r="12" fill="none" stroke="#222831" stroke-width="3"/><path d="M14 7v7l5 3" fill="none" stroke="#222831" stroke-width="3"/></svg></div>
  <h3 style="left:18px">HOURS OF OPERATION</h3>
  <ul class="rows">
    <li><b>MONDAY</b><span>8:00am - 6:00pm</span></li>
    <li><b>TUESDAY</b><span>8:00am - 6:00pm</span></li>
    <li><b>WEDNESDAY</b><span>8:00am - 6:00pm</span></li>
    <li><b>THURSDAY</b><span>8:00am - 6:00pm</span></li>
    <li><b>FRIDAY</b><span>8:00am - 6:00pm</span></li>
    <li><b>SATURDAY</b><span>9:00am - 4:00pm</span></li>
    <li><b>SUNDAY</b><span>9:00am - 4:00pm</span></li>
  </ul>
</section>

<section class="abs info contact">
  <div class="badge" style="left:48px;background:var(--blue)"><svg width="30" height="22" viewBox="0 0 30 22"><rect x="1" y="1" width="28" height="20" fill="#fff"/><path d="M1 1l14 11L29 1" fill="none" stroke="#5fc3ec" stroke-width="2"/></svg></div>
  <h3 style="left:46px">CONTACT INFORMATION</h3>
  <ul class="rows">
    <li><b>TELEPHONE</b><span>555 010 0199</span></li>
    <li><b>FAX</b><span>555 010 0199</span></li>
    <li><b>EMAIL</b><span>hello@mendwell.co</span></li>
    <li class="tall"><b>ADDRESS</b><span>48 Alder Row,<br>Fernbrook,<br>Canada, R2B 4K7</span></li>
    <li><b>DIRECTIONS</b><span>Map Directions</span></li>
  </ul>
</section>

<section class="abs about">
  <div class="abs sec-title" style="top:74px"><small>ABOUT</small><h2>OUR CLINIC</h2><i></i></div>
  <div class="about-text">
    <p>Lorem Ipsum is simply dummy text of the printing and typesetting industry. Lorem Ipsum has been the industry's standard dummy text ever since the 1500s, when an unknown printer took a galley of type and scrambled it to make a type specimen book. It has survived not but also the leap into electronic typesetdesktop publishing software like Pagecraft Studio including versions of Lorem Ipsum.</p>
    <p>Lorem Ipsum is simply dummy text of the printing and typesetting industry. It has survived not only five centuries, but also the leap into electronic desktop publishing software like Pagecraft Studio including versions of Lorem Ipsum.</p>
  </div>
</section>

<section class="abs team">
  <div class="col-head" style="left:72px"><svg width="16" height="18" viewBox="0 0 16 18"><path d="M8 1c-4 0-5 3-5 6v4l-2 3h14l-2-3V7c0-3-1-6-5-6z" fill="#5fc3ec"/><circle cx="8" cy="16" r="2" fill="#5fc3ec"/></svg>ALERTS</div>
  <div class="pager" style="left:380px">‹›</div>
  <div class="col-head" style="left:434px"><svg width="22" height="18" viewBox="0 0 22 18"><circle cx="7" cy="5" r="4" fill="#5fc3ec"/><circle cx="16" cy="5" r="3.5" fill="#5fc3ec"/><path d="M0 18c0-6 3-8 7-8s7 2 7 8z" fill="#5fc3ec"/><path d="M15 10c4 0 7 2 7 7h-6c0-3-1-5-3-6z" fill="#5fc3ec"/></svg>OUR STAFF</div>
  <div class="pager" style="left:1100px">‹›</div>

  <div class="alert" style="top:115px"><div class="date"><b>02</b><span>MAR 15</span></div><h4>A HANDY LOREM IPSUM GENTOR<br>FOR ALL LAYOUT NEEDS</h4><p>Lorem Ipsum is simply dummy text of<br>and typesetting industry.</p></div>
  <div class="alert" style="top:243px"><div class="date"><b>02</b><span>MAR 15</span></div><h4>A HANDY LOREM IPSUM GENTOR<br>FOR ALL LAYOUT NEEDS</h4><p>Lorem Ipsum is simply dummy text of<br>and typesetting industry.</p></div>
  <div class="alert" style="top:370px"><div class="date"><b>02</b><span>MAR 15</span></div><h4>A HANDY LOREM IPSUM GENTOR<br>FOR ALL LAYOUT NEEDS</h4><p>Lorem Ipsum is simply dummy text of<br>and typesetting industry.</p></div>

  <div class="staff" style="left:434px;top:112px"><div class="photo" role="img" aria-label="Staff portrait of a physician in scrubs"></div><h4>DR. JOHN SMITH, MD</h4><span>Physician</span><a href="#">Read more ›</a></div>
  <div class="staff" style="left:790px;top:112px"><div class="photo" role="img" aria-label="Staff portrait of a physician in scrubs"></div><h4>DR. JOHN SMITH, MD</h4><span>Physician</span><a href="#">Read more ›</a></div>
  <div class="staff" style="left:434px;top:288px"><div class="photo" role="img" aria-label="Staff portrait of a physician in scrubs"></div><h4>DR. JOHN SMITH, MD</h4><span>Physician</span><a href="#">Read more ›</a></div>
  <div class="staff" style="left:790px;top:288px"><div class="photo" role="img" aria-label="Staff portrait of a physician in scrubs"></div><h4>DR. JOHN SMITH, MD</h4><span>Physician</span><a href="#">Read more ›</a></div>
</section>

<section class="abs policies">
  <div class="abs sec-title" style="top:52px"><small>CLINIC</small><h2>POLICIES</h2><i></i></div>
  <div class="policy" style="left:72px">
    <svg width="20" height="26" viewBox="0 0 20 26"><path d="M1 1h12l6 6v18H1z" fill="none" stroke="#5fc3ec" stroke-width="2"/><path d="M5 12h10M5 16h10M5 20h10" stroke="#5fc3ec" stroke-width="2"/></svg>
    <h4>LATE ARRIVALS</h4>
    <p>Lorem Ipsum is simply dummy text of and typesetting industry. Lorem Ipsum is simply dummy text of and typesetting industry.</p>
    <a href="#">Read more ›</a>
  </div>
  <div class="policy" style="left:434px">
    <svg width="26" height="24" viewBox="0 0 26 24"><path d="M13 1 25 23H1z" fill="#5fc3ec"/><path d="M13 9v7M13 18v2" stroke="#fff" stroke-width="2.5"/></svg>
    <h4>MISSED APPOINTMENTS</h4>
    <p>Lorem Ipsum is simply dummy text of and typesetting industry. Lorem Ipsum is simply dummy text of and typesetting industry.</p>
    <a href="#">Read more ›</a>
  </div>
  <div class="policy" style="left:795px">
    <svg width="28" height="20" viewBox="0 0 28 20"><rect x="1" y="1" width="26" height="18" rx="2" fill="none" stroke="#5fc3ec" stroke-width="2"/><path d="M1 7h26" stroke="#5fc3ec" stroke-width="4"/></svg>
    <h4>FEES</h4>
    <p>Lorem Ipsum is simply dummy text of and typesetting industry. Lorem Ipsum is simply dummy text of and typesetting industry.</p>
    <a href="#">Read more ›</a>
  </div>
  <a class="btn-blue" href="#">VIEW ALL CLINIC POLICIES</a>
</section>

<section class="abs location">
  <div class="abs sec-title" style="top:44px"><small>OUR</small><h2>LOCATION</h2><i></i></div>
</section>

<section class="abs map" role="img" aria-label="Street map showing the clinic location">
  <div class="map-card"><b>Clinic Name</b>48 Alder Row, Fernbrook,<br>Canada, R2B 4K7<i></i></div>
</section>

<footer class="abs footer">
  <span style="left:72px">©2015 Clinic Name. All Rights Reserved</span>
  <span style="left:940px">Terms &amp; Privacy Policy | Sitemap</span>
</footer>

</body>
</html>
```